Hemp company needs website/online store

We are a startup hemp company and we need an online storefront designed. We are very open do design, but will include our logo to help. We make 100% hemp derived products like edibles, concentrates, vapes and THCA flower. Everything is grown locally, and all products are extracted and made in house.

• I would like to highlight that we have Cannabis products that are hemp derived and 100% legal across the US. Also that all cannabis is locally grown and products are extracted and made in house and sent out for third party lab testing.

```html
<!DOCTYPE html>
<html lang="en">
<head>
<meta charset="utf-8">
<title>Sunny Grove Hemp</title>
<link href="https://fonts.googleapis.com/css2?family=Fredoka:wght@500;600&family=Poppins:wght@400;500;600&display=swap" rel="stylesheet">
<style>
:root{
  --green:#7ba52f;
  --green-dark:#5f8a22;
  --green-deep:#3f6b1c;
  --lime:#9cc23d;
  --ink:#222;
  --text:#444;
  --pale:#f1f4ec;
  --white:#fff;
  --footer:#2a2a2a;
}
*{box-sizing:border-box;margin:0;padding:0}
html,body{width:1200px;height:5068px;overflow:hidden}
body{font-family:"Poppins",sans-serif;color:var(--text);background:var(--white);position:relative}
.h{font-family:"Fredoka",sans-serif;font-weight:600}
section,header,footer{position:absolute;left:0;width:1200px}
.abs{position:absolute}
.fill{position:absolute}
.btn{position:absolute;display:flex;align-items:center;gap:6px;justify-content:center;background:var(--green);color:#fff;font-weight:600;font-size:13px;border-radius:22px;height:40px;padding:0 18px;box-shadow:0 3px 0 var(--green-deep)}
.btn .arr{width:14px;height:14px;border-radius:50%;background:#fff;display:inline-flex;align-items:center;justify-content:center}
.sec-title{position:absolute;left:0;width:1200px;text-align:center;font-size:36px;color:var(--ink)}
.sec-title .mark{display:inline-block;width:26px;height:26px;border:3px solid var(--green);border-radius:4px;margin-right:8px;vertical-align:-2px}
.small{font-size:11.5px;line-height:20px}

/* top bar + header */
.topbar{top:0;height:44px;background:linear-gradient(90deg,var(--green-dark),var(--lime));color:#fff;font-size:14px;text-align:center;line-height:44px;font-weight:500}
.header{top:44px;height:98px;background:#fff}
.logo{left:110px;top:22px;font-size:30px;color:var(--green-dark)}
.logo small{display:block;font-size:12px;letter-spacing:7px;text-align:right;margin-top:-6px}
.logo-square{position:absolute;left:44px;top:-14px;width:26px;height:26px;border:3px solid var(--green);border-radius:3px;background:#fff}
.nav{left:289px;top:0;height:98px;display:flex;font-size:13px;color:var(--ink)}
.nav a{display:flex;align-items:center;padding:0 16px;text-decoration:none;color:inherit}
.nav a.on{background:var(--green);color:#fff;width:72px;justify-content:center}
.search{left:812px;top:34px;width:192px;height:34px;border:2px solid var(--green);border-radius:18px;font-size:11px;display:flex;align-items:center;gap:8px;padding-left:6px;color:var(--ink)}
.search i{width:22px;height:22px;border-radius:50%;background:var(--green);display:inline-block}
.icon-c{width:32px;height:32px;border-radius:50%;background:var(--green);top:35px}

/* hero */
.hero{top:142px;height:600px;overflow:hidden}
.hero-bg{inset:0;background:radial-gradient(circle at 75% 45%,#8a5a20 0,#3d3a1a 25%,#121410 55%,#050505 100%)}
.hero h1{left:102px;top:170px;color:#fff;font-size:48px;line-height:60px;letter-spacing:1px}
.hero h1 span{font-size:24px;color:var(--lime);margin-left:12px}
.hero p{left:104px;top:312px;width:360px;color:#eee;font-size:12px;line-height:22px}
.dots{left:576px;top:528px;display:flex;gap:6px}
.dots i{width:11px;height:11px;border-radius:50%;border:2px solid #fff}
.dots i.f{background:#fff}

/* about */
.about{top:742px;height:541px}
.about h2{left:642px;top:88px;font-size:34px;color:var(--green-dark)}
.about h2 small{font-size:13px;margin-left:6px}
.about p{left:642px;width:450px;color:var(--text)}

/* products */
.products{top:1283px;height:688px;background:linear-gradient(180deg,var(--green-deep),var(--green))}
.products .sec-title{color:#fff}
.card{position:absolute;top:236px;width:234px;height:354px;background:#fff;text-align:center}
.card .img{height:167px}
.card h3{font-size:19px;color:var(--green-dark);margin-top:20px}
.card p{font-size:10.5px;line-height:18px;padding:8px 12px 0}
.card .btn{left:66px;top:296px;height:32px;font-size:11px}

/* testimonials */
.testi{top:1971px;height:462px}
.tcard{position:absolute;top:157px;width:470px;height:217px;border:2px solid #b6cc8c;padding:40px 26px 0 26px}
.tcard .q{position:absolute;left:18px;top:12px;font-size:28px;color:var(--green);font-family:Georgia,serif}
.tcard .who{position:absolute;left:26px;bottom:22px;color:var(--green-dark);font-weight:500;font-size:14px}
.tcard .stars{position:absolute;right:26px;bottom:24px;color:#e2a800;font-size:12px;letter-spacing:1px}

/* highlight */
.legal{top:2433px;height:532px;background:var(--pale)}
.legal .msg{left:610px;top:140px;width:560px;font-family:"Fredoka",sans-serif;font-weight:500;font-size:27px;line-height:36px;color:var(--green-dark)}

/* contact */
.contact{top:2965px;height:619px;background:linear-gradient(180deg,var(--green-dark),var(--green))}
.contact .sec-title{color:#fff}
.cinfo{left:191px;top:200px;color:#fff}
.cinfo h3{font-size:27px;font-weight:500}
.crow{position:absolute;left:0;display:flex;gap:10px;width:300px}
.crow i{width:30px;height:30px;border-radius:50%;border:2px solid #fff;flex:none;display:flex;align-items:center;justify-content:center}
.crow b{font-weight:500;font-size:14px}
.crow div{font-size:14px;line-height:22px}
.field{position:absolute;height:43px;background:#fff;font-size:12px;padding:14px 12px;color:#555}
.btn.ghost{background:transparent;border:2px solid #fff;box-shadow:none}

/* blog */
.blog{top:3584px;height:655px}
.bcard{position:absolute;top:173px;width:307px;height:397px;background:#fff;box-shadow:0 0 8px rgba(0,0,0,.08)}
.bcard .img{height:199px}
.bcard h3{font-family:"Fredoka",sans-serif;font-weight:500;font-size:16px;color:var(--green-dark);padding:16px 18px 0;line-height:22px}
.bcard p{font-size:10.5px;line-height:18px;padding:8px 18px 0}
.bcard .btn{left:18px;top:342px;height:36px}

/* newsletter */
.news{top:4239px;height:413px;background:var(--green)}
.news h2{left:678px;top:62px;color:#fff;font-size:34px;line-height:40px;font-weight:600}
.news p{left:678px;top:160px;width:420px;color:#fff;font-size:10.5px;line-height:20px}
.news .inp{left:680px;top:235px;width:420px;height:44px;border:1.5px solid #fff;border-radius:22px;color:#fff;font-size:12px;padding:14px 18px}

/* footer */
.footer{top:4652px;height:416px;background:var(--footer);color:#eee}
.fcol{position:absolute;top:72px}
.fcol h4{font-family:"Fredoka",sans-serif;font-weight:600;color:var(--lime);font-size:24px;margin-bottom:18px}
.fcol a{display:block;color:#eee;font-size:13px;line-height:30px;text-decoration:none}
.pay{display:flex;gap:8px;position:absolute;left:832px;top:368px}
.pay i{width:38px;height:24px;border-radius:3px;background:#e6e6e6}
</style>
</head>
<body>

<div class="topbar">Free Shipping On All Orders $49.99+</div>

<header class="header">
  <div class="abs logo h"><span class="logo-square"></span>Sunny Grove<small>HEMP</small></div>
  <nav class="abs nav">
    <a class="on" href="#">Home</a><a href="#">About Us</a><a href="#">Our Products</a><a href="#">Testimonials</a><a href="#">Contact Us</a>
  </nav>
  <div class="abs search"><i></i>Search Products</div>
  <div class="abs icon-c" style="left:1014px"></div>
  <div class="abs icon-c" style="left:1062px"></div>
</header>

<section class="hero">
  <div class="fill hero-bg" role="img" aria-label="Glass jar of colourful hemp gummies with green hemp leaves on a dark background"></div>
  <h1 class="abs h">Welcome TO<br>Sunny Grove<span>Hemp</span></h1>
  <p class="abs">Lorem ipsum dolor sit amet, consectetur adipiscing elit, sed do eiusmod tempor incididunt ut labore et dolore magna aliqua.</p>
  <a class="btn" style="left:104px;top:408px">Shop Now <span class="arr"></span></a>
  <div class="abs dots"><i></i><i class="f"></i><i class="f"></i></div>
</section>

<section class="about">
  <div class="fill" style="left:128px;top:74px;width:413px;height:394px;background:radial-gradient(circle,#7fae3a,#4b7d22 60%,#fff 72%)" role="img" aria-label="Large green hemp leaf illustration inside a square frame"></div>
  <h2 class="abs h">About Sunny Grove<small>HEMP</small></h2>
  <p class="abs small" style="top:156px">Lorem ipsum dolor sit amet, consectetur adipiscing elit, sed do eiusmod tempor incididunt ut labore et dolore magna aliqua. Quis ipsum suspendisse ultrices gravida. Risus commodo viverra maecenas accumsan lacus vel facilisis.</p>
  <p class="abs small" style="top:224px">Sed ut perspiciatis unde omnis iste natus error sit voluptatem accusantium doloremque laudantium, totam rem aperiam, eaque ipsa quae ab illo inventore veritatis et quasi architecto beatae vitae dicta sunt explicabo. Nemo enim ipsam voluptatem quia voluptas sit aspernatur aut odit aut fugit, sed quia consequuntur magni dolores eos qui ratione voluptatem sequi nesciunt. Neque porro quisquam est, qui dolorem ipsum quia dolor sit amet, consectetur, adipisci velit, sed quia non numquam eius modi tempora incidunt ut labore et dolore magnam aliquam quaerat voluptatem.</p>
  <a class="btn" style="left:642px;top:388px">Read More <span class="arr"></span></a>
  <div class="fill" style="left:836px;top:410px;width:364px;height:131px;background:radial-gradient(ellipse,#e0463a,#f0a93a 45%,rgba(255,255,255,0) 72%)" role="img" aria-label="Bowl of colourful gummy bears"></div>
</section>

<section class="products">
  <div class="sec-title h" style="top:92px"><span class="mark" style="border-color:#fff"></span>Our Products</div>
  <p class="abs small" style="left:180px;top:160px;width:840px;text-align:center;color:#fff">Lorem ipsum dolor sit amet, consectetur adipiscing elit, sed do eiusmod tempor incididunt ut labore et dolore magna aliqua. Quis ipsum suspendisse ultrices gravida. Risus commodo viverra maecenas accumsan lacus vel facilisis.</p>
  <div class="card" style="left:104px"><div class="img" role="img" aria-label="Scattered gummy candies" style="background:linear-gradient(135deg,#fbe4e4,#f6b25a,#fde3e0)"></div><h3 class="h">Edibles</h3><p>Lorem ipsum dolor sit amet, consectetur adipiscing elit, sed do eiusmod tempor incididunt aliqua.</p><a class="btn">Shop Now <span class="arr"></span></a></div>
  <div class="card" style="left:356px"><div class="img" role="img" aria-label="Jar of golden concentrate" style="background:radial-gradient(circle,#f2b80a,#f7e9b0 45%,#f6f6f6 70%)"></div><h3 class="h">Concentrates</h3><p>Lorem ipsum dolor sit amet, consectetur adipiscing elit, sed do eiusmod tempor incididunt aliqua.</p><a class="btn">Shop Now <span class="arr"></span></a></div>
  <div class="card" style="left:608px"><div class="img" role="img" aria-label="Vape cartridge" style="background:linear-gradient(90deg,#eee 40%,#2d4f7a 48%,#222 52%,#eee 60%)"></div><h3 class="h">Vapes</h3><p>Lorem ipsum dolor sit amet, consectetur adipiscing elit, sed do eiusmod tempor incididunt aliqua.</p><a class="btn">Shop Now <span class="arr"></span></a></div>
  <div class="card" style="left:860px"><div class="img" role="img" aria-label="Dried THCA flower bud" style="background:radial-gradient(ellipse 30% 45%,#8a6b3c,#6b7a3a 60%,#fff 100%)"></div><h3 class="h">THCA Flowers</h3><p>Lorem ipsum dolor sit amet, consectetur adipiscing elit, sed do eiusmod tempor incididunt aliqua.</p><a class="btn">Shop Now <span class="arr"></span></a></div>
  <div class="fill" style="left:0;top:580px;width:220px;height:130px;background:radial-gradient(ellipse,#e4573a,#f0b640 45%,rgba(123,165,47,0) 72%)" role="img" aria-label="Pile of gummy candies"></div>
</section>

<section class="testi">
  <div class="sec-title h" style="top:62px"><span class="mark"></span>Client Testimonial</div>
  <div class="tcard" style="left:118px"><span class="q">“</span><p class="small">Lorem ipsum dolor sit amet, consectetur adipiscing elit, sed do eiusmod tempor incididunt ut labore et dolore magna aliqua. Ut enim ad minim veniam, quis nostrud exercitation ullamco laboris nisi ut aliquip ex ea commodo consequat. Duis aute irure dolor in reprehenderit in voluptate velit esse cillum dolore eu fugiat nulla pariatur.</p><span class="who h">- Mara Quill</span><span class="stars">★★★★★</span></div>
  <div class="tcard" style="left:622px"><span class="q">“</span><p class="small">Lorem ipsum dolor sit amet, consectetur adipiscing elit, sed do eiusmod tempor incididunt ut labore et dolore magna aliqua. Ut enim ad minim veniam, quis nostrud exercitation ullamco laboris nisi ut aliquip ex ea commodo consequat. Duis aute irure dolor in reprehenderit in voluptate velit esse cillum dolore eu fugiat nulla pariatur.</p><span class="who h">- Mara Quill</span><span class="stars">★★★★★</span></div>
  <div class="fill" style="left:976px;top:380px;width:224px;height:140px;background:radial-gradient(ellipse,#c8345a,#8fc53a 45%,rgba(255,255,255,0) 72%)" role="img" aria-label="Colourful gummy cubes"></div>
</section>

<section class="legal">
  <div class="fill" style="left:40px;top:160px;width:260px;height:260px;background:radial-gradient(circle,#7fae3a,#5f8a22 50%,rgba(241,244,236,0) 70%)" role="img" aria-label="Green hemp leaf illustration"></div>
  <div class="fill" style="left:102px;top:81px;width:223px;height:226px;background:linear-gradient(135deg,#6a8f3a,#e0b89a,#7b3b6a)" role="img" aria-label="Hand holding hemp gummies over hemp leaves"></div>
  <div class="fill" style="left:338px;top:183px;width:225px;height:236px;background:linear-gradient(135deg,#c9c9b8,#7d8a4a,#d8d3c4)" role="img" aria-label="Dried hemp flower and a vape cartridge on a table"></div>
  <p class="abs msg">We Have Cannabis Products That Are Hemp Derived And 100% Legal Across The US. Also That All Cannabis Is Locally Grown And Products Are Extracted And Made In House And Sent Out For Third Party Lab Testing.</p>
</section>

<section class="contact">
  <div class="sec-title h" style="top:100px"><span class="mark" style="border-color:#fff"></span>Contact Us</div>
  <div class="abs cinfo">
    <h3 class="h">Contact Information</h3>
    <div class="crow" style="top:70px"><i></i><div><b>Address :</b><br>0612 Lorem ipsum dolor sit amet, consectetur 2003</div></div>
    <div class="crow" style="top:170px"><i></i><div><b>Phone Number :</b><br>+1 888 888 8888</div></div>
    <div class="crow" style="top:250px"><i></i><div><b>Email :</b><br>info@sunnygrovehemp.example</div></div>
  </div>
  <div class="field" style="left:533px;top:188px;width:266px">First Name</div>
  <div class="field" style="left:812px;top:188px;width:266px">Last Name</div>
  <div class="field" style="left:533px;top:245px;width:266px">Phone Number</div>
  <div class="field" style="left:812px;top:245px;width:266px">Email</div>
  <div class="field" style="left:533px;top:302px;width:266px">Country</div>
  <div class="field" style="left:812px;top:302px;width:266px">Zip Code</div>
  <div class="field" style="left:533px;top:359px;width:545px;height:93px">Message</div>
  <a class="btn ghost" style="left:533px;top:469px;width:126px">Submit <span class="arr"></span></a>
</section>

<section class="blog">
  <div class="sec-title h" style="top:80px"><span class="mark"></span>Our Blog</div>
  <div class="bcard" style="left:114px"><div class="img" role="img" aria-label="Vape cartridge among hemp leaves" style="background:linear-gradient(135deg,#eef0e6,#8aa25a,#c4a85a)"></div><h3>Lorem ipsum dolor sit amet, consectetur adipiscing elit, sed</h3><p>Ut labore et dolore magna aliqua. Ut enim ad minim veniam, quis nostrud exercitation ullamco laboris nisi ut aliquip ex ea commodo consequat.</p><a class="btn">Read More <span class="arr"></span></a></div>
  <div class="bcard" style="left:445px"><div class="img" role="img" aria-label="Colourful gummy cubes with a hemp leaf" style="background:linear-gradient(135deg,#d8a6e0,#7fb04a,#f0c0d8)"></div><h3>Lorem ipsum dolor sit amet, consectetur adipiscing elit, sed</h3><p>Ut labore et dolore magna aliqua. Ut enim ad minim veniam, quis nostrud exercitation ullamco laboris nisi ut aliquip ex ea commodo consequat.</p><a class="btn">Read More <span class="arr"></span></a></div>
  <div class="bcard" style="left:775px"><div class="img" role="img" aria-label="Amber hemp concentrate with a leaf" style="background:linear-gradient(135deg,#3a1c08,#c2701a,#2a1a0a)"></div><h3>Lorem ipsum dolor sit amet, consectetur adipiscing elit, sed</h3><p>Ut labore et dolore magna aliqua. Ut enim ad minim veniam, quis nostrud exercitation ullamco laboris nisi ut aliquip ex ea commodo consequat.</p><a class="btn">Read More <span class="arr"></span></a></div>
</section>

<section class="news">
  <div class="fill" style="left:0;top:0;width:630px;height:413px;background:linear-gradient(135deg,#f4e2d4,#e8621e 40%,#2fa58a 70%,#c4d0d0)" role="img" aria-label="Close-up of colourful gummy bears on a plate"></div>
  <h2 class="abs h">Subscribe To Our<br>Newsletter</h2>
  <p class="abs">Lorem ipsum dolor sit amet, consectetur adipiscing elit, sed do eiusmod tempor incididunt ut labore et dolore magna aliqua. Quis ipsum suspendisse ultrices gravida.</p>
  <div class="abs inp">Enter Email</div>
  <a class="btn ghost" style="left:680px;top:298px;width:130px">Submit <span class="arr"></span></a>
</section>

<footer class="footer">
  <div class="fcol" style="left:104px"><h4>Quick Links</h4><a>Home</a><a>About Us</a><a>Our Products</a><a>Testimonials</a><a>Contact Us</a></div>
  <div class="fcol" style="left:305px"><h4>Help Links</h4><a>Privacy Policy</a><a>Terms of Service</a><a>Return Policy</a><a>Shop</a><a>Login</a></div>
  <div class="fcol" style="left:504px;width:300px"><h4>Contact Us</h4>
    <div class="crow" style="position:relative;color:#eee"><i></i><div><b>Address :</b><br>0612 Lorem ipsum dolor sit amet, consectetur 2003</div></div>
    <div class="crow" style="position:relative;margin-top:14px;color:#eee"><i></i><div><b>Phone Number :</b><br>+1 888 888 8888</div></div>
    <div class="crow" style="position:relative;margin-top:14px;color:#eee"><i></i><div><b>Email :</b><br>info@sunnygrovehemp.example</div></div>
  </div>
  <div class="abs h" style="left:850px;top:150px;font-size:38px;color:var(--lime)">Sunny Grove</div>
  <div class="abs h" style="left:848px;top:232px;font-size:24px;color:var(--lime)">Follow Us</div>
  <div class="abs" style="left:850px;top:272px;display:flex;gap:6px"><i style="width:24px;height:24px;border:1.5px solid #eee;border-radius:50%"></i><i style="width:24px;height:24px;border:1.5px solid #eee;border-radius:50%"></i><i style="width:24px;height:24px;border:1.5px solid #eee;border-radius:50%"></i></div>
  <div class="abs" style="left:104px;top:373px;font-size:12px">©Copyrights 2023 Company Name | All Rights Reserved</div>
  <div class="pay"><i></i><i></i><i></i><i></i><i></i><i></i></div>
</footer>

</body>
</html>
```